Small Business Consulting Firm Needs Letterhead

We need a letterhead for our company "Brightpath Plus". Our company does outbound calling and mailing to business owner's companies who have taken high interest loans. These loans tend to put these businesses in a big financial bind short term, and we help them find better financial options. We would like the design to match our colors of our logo. Headers and footers would look nice, but we are open. We would want it to include our address, website, phone, and email info. Our address - 2000 E. Lamar Blvd. Suite 600Website - www.safeguardtoday.comEmail - info@safeguardtoday.comPhone - 855-726-1938
Industry/Entity Type
Financial Planning
Look and feel
Each slider illustrates characteristics of the customer's brand and the style your logo design should communicate.

```html
<!DOCTYPE html>
<html lang="en">
<head>
<meta charset="utf-8">
<title>Brightpath Plus Letterhead</title>
<link href="https://fonts.googleapis.com/css2?family=Open+Sans:wght@400;600&family=Lato:wght@400;700&display=swap" rel="stylesheet">
<style>
  :root {
    --backdrop: #e6e7e8;
    --paper: #ffffff;
    --ink: #3a3a3a;
    --ink-soft: #4a4a4a;
    --brand-green: #6cc04a;
    --brand-green-dark: #4fa534;
    --brand-blue: #1b75bc;
    --rule: #9a9a9a;
  }
  * { box-sizing: border-box; margin: 0; padding: 0; }
  html, body { width: 1040px; height: 1200px; overflow: hidden; background: var(--backdrop); }
  body { position: relative; font-family: "Open Sans", Arial, sans-serif; color: var(--ink); }

  .letterhead {
    position: absolute; left: 69px; top: 20px; width: 902px; height: 1160px;
    background: var(--paper); box-shadow: 0 2px 10px rgba(0,0,0,.12);
  }
  .side-band {
    position: absolute; left: 0; top: 0; width: 33px; height: 100%;
    background: linear-gradient(90deg, var(--brand-green) 0%, var(--brand-green-dark) 60%, var(--brand-blue) 100%);
  }

  .brand { position: absolute; left: 0; right: 0; top: 38px; text-align: center; }
  .brand-mark { display: block; width: 56px; height: 56px; margin: 0 auto 22px; background: var(--brand-green); }
  .brand-name { font-size: 18px; font-weight: 400; letter-spacing: 2px; text-transform: uppercase; color: var(--ink); }

  .letter { position: absolute; left: 85px; width: 728px; font-size: 14px; color: var(--ink-soft); }
  .issue-date { top: 208px; }
  .recipient { top: 244px; line-height: 17px; }
  .salutation { top: 344px; }
  .body-copy { top: 396px; line-height: 26px; text-align: justify; hyphens: auto; -webkit-hyphens: auto; }
  .body-copy p + p { margin-top: 26px; }
  .closing { top: 788px; }
  .signatory { top: 860px; }
  .signatory-name { font-size: 18px; font-weight: 600; color: var(--ink); }
  .signatory-title { font-size: 14px; margin-top: 4px; }

  .footer { position: absolute; left: 102px; width: 723px; top: 1088px; text-align: center; font-family: "Lato", Arial, sans-serif; }
  .footer-address { font-size: 17px; color: #222; }
  .footer-rule { height: 1px; background: var(--rule); margin: 5px 0 6px; }
  .footer-contact { font-size: 17px; color: #222; }
  .footer-contact .label { color: var(--brand-blue); font-weight: 700; }
  .footer-contact .web { color: var(--brand-blue); }
  .footer-contact .web em { font-style: normal; color: var(--brand-green); }
</style>
</head>
<body>
  <main class="letterhead">
    <div class="side-band" role="img" aria-label="Vertical decorative band of green and blue geometric tiles"></div>

    <header class="brand">
      <span class="brand-mark"></span>
      <div class="brand-name">Brightpath Plus</div>
    </header>

    <div class="letter issue-date">Issuing Date: May 5, 2018</div>
    <div class="letter recipient">
      Name Of Employee Mr. XYZABC<br>
      Address of Employee<br>
      Address Line 2 etc..
    </div>
    <div class="letter salutation">Dear Mr.XYZABC</div>

    <div class="letter body-copy">
      <p>Lorem Ipsum has been the industry's standard dummy text ever since the 1500s, when an unknown printer took a galley of type and scrambled it to make a type specimen book. It has survived not only five centuries, but also the leap into electronic typesetting, remaining essentially unchanged. It was popularised in the 1960s with the release of Versaret sheets containing Lorem Ipsum passages, and more recently with desktop publishing software like Orvel PageCraft including versions of Lorem Ipsum.</p>
      <p>Lorem Ipsum is simply dummy text of the printing and typesetting industry. Lorem Ipsum has been the industry's standard dummy text ever since the 1500s, when an unknown printer took a galley of type and scrambled it to make a type specimen book.</p>
      <p>It has survived not only five centuries, but also the leap into electronic typesetting, remaining essentially unchanged. It was popularised in the 1960s with the release of Versaret sheets containing Lorem IpsumIpsum passages.</p>
    </div>

    <div class="letter closing">Yours Sincerely</div>
    <div class="letter signatory">
      <div class="signatory-name">Marcus Ellery</div>
      <div class="signatory-title">Managing Director</div>
    </div>

    <footer class="footer">
      <div class="footer-address">4170 W. Corwin Ave. Suite 310</div>
      <div class="footer-rule"></div>
      <div class="footer-contact">
        <span class="label">P:</span> 855-726-1938 &nbsp;| <span class="label">E:</span> info@brightpathplus.com | <span class="web">www.<em>brightpathplus</em>.com</span>
      </div>
    </footer>
  </main>
</body>
</html>
```